Book Cover for a Short Story called “Leaving Harbor"

Pretty Straightforward. Looking for a 5.5X8.5 book cover. The story is a very short (40 pages) story about a man who moves from Greece to Canada in 1920. I have three photos to provide. One is the house that he left in greece. THen I have photos of him and his wife who he met in Toronto. I think I want the house photo on the front...
I will need cover for paper back and e-book. The ISBN numbers are:

ISBN: 978-1-5523094-2-7 (e-book)
ISBN: 978-1-5523094-1-0 (paperback)

If you want you can read it at https://kevinmarlow.example/fiction/leaving-harbor/

Colors
0094D4
00A9DD
6FCCEA
C7EBF8
E9F6FB

Requirements
Must have
• Room for a blurb about the book on the back cover. ISBN Number

```html
<!DOCTYPE html>
<html lang="en">
<head>
<meta charset="utf-8">
<title>Leaving Harbor – Cover Spread</title>
<link rel="stylesheet" href="https://fonts.googleapis.com/css2?family=EB+Garamond:wght@400;500&display=swap">
<style>
  :root {
    --backdrop: #4a4a4a;
    --paper: #ffffff;
    --ink: #1d1d1f;
    --wash-pale: #c7ebf8;
    --wash-light: #6fccea;
    --wash-mid: #00a9dd;
    --wash-deep: #0094d4;
    --wash-shadow: #2f7fbf;
    --title: #ffffff;
  }
  * { margin: 0; padding: 0; box-sizing: border-box; }
  html, body {
    width: 1200px; height: 761px; overflow: hidden;
    background: var(--backdrop);
  }
  .cover-spread {
    position: absolute; left: 140px; top: 25px;
    width: 920px; height: 710px;
    background: var(--paper);
    overflow: hidden;
    font-family: "EB Garamond", Georgia, serif;
  }
  .watercolor-band { position: absolute; inset: 0; width: 920px; height: 710px; }
  .author-portrait {
    position: absolute; left: 0; top: 187px; width: 245px; height: 347px;
    background: linear-gradient(180deg, #8a8f96 0%, #b08f80 18%, #6d7785 30%, #243149 48%, #1b2438 100%);
    clip-path: polygon(70px 0, 118px 4, 140px 30px, 140px 100px, 152px 124px, 178px 148px, 188px 200px, 198px 238px, 245px 244px, 245px 300px, 178px 304px, 170px 330px, 100px 347px, 30px 340px, 0 330px, 0 122px, 42px 104px, 46px 40px);
  }
  .house-photo {
    position: absolute; left: 496px; top: 282px; width: 424px; height: 300px;
    background: linear-gradient(180deg, rgba(47,127,191,0.15) 0%, rgba(30,98,160,0.45) 45%, rgba(111,204,234,0.35) 100%);
  }
  .back-title, .front-title {
    position: absolute; color: var(--title); font-weight: 400;
    white-space: nowrap; line-height: 1; letter-spacing: 0.5px;
  }
  .back-title { left: 177px; top: 186px; font-size: 39px; }
  .front-title { left: 498px; top: 212px; font-size: 57px; }
  .blurb {
    position: absolute; color: var(--title);
    font-size: 13.2px; line-height: 14.7px; text-align: justify;
    hyphens: none;
  }
  .blurb-lead { left: 190px; top: 239px; width: 239px; }
  .blurb-more { left: 252px; top: 370px; width: 177px; }
  .isbn {
    position: absolute; left: 32px; top: 648px;
    font-size: 10.5px; color: var(--ink);
  }
  .author-name {
    position: absolute; left: 593px; top: 632px; width: 200px;
    text-align: center; font-size: 20px; letter-spacing: 3px;
    color: var(--ink); text-transform: uppercase; white-space: nowrap;
  }
</style>
</head>
<body>
<main class="cover-spread">
  <svg class="watercolor-band" viewBox="0 0 920 710" aria-hidden="true">
    <path fill="var(--wash-pale)" d="M0 68 C40 70 70 60 110 72 C140 66 160 78 190 74 C220 70 250 66 280 70 C300 62 330 64 360 84 C390 98 420 120 450 150 C480 164 510 160 540 150 C570 140 600 120 640 96 C680 80 720 90 760 72 C800 66 860 74 920 68 L920 600 L0 600 Z"/>
    <path fill="var(--wash-light)" d="M0 110 C30 100 60 108 90 118 C120 110 150 96 180 104 C210 110 240 112 270 118 C300 122 330 116 360 130 C390 140 420 160 450 170 C480 176 510 168 540 160 C570 150 600 130 630 116 C660 108 700 112 730 104 C770 98 820 108 860 100 C890 96 905 104 920 100 L920 600 L0 600 Z"/>
    <path fill="var(--wash-mid)" d="M0 150 C40 140 80 150 120 160 C160 150 200 144 240 150 C280 156 320 158 360 164 C400 172 440 180 480 178 C520 176 560 170 600 166 C640 160 680 150 720 160 C770 170 830 156 880 164 C900 168 910 166 920 168 L920 560 L0 560 Z" opacity="0.85"/>
    <path fill="var(--wash-deep)" d="M0 220 C60 210 120 226 180 222 C240 218 300 232 360 230 C420 228 480 240 540 236 C600 232 660 242 720 232 C780 224 850 236 920 230 L920 520 L0 520 Z" opacity="0.55"/>
    <path fill="var(--wash-shadow)" d="M0 280 C80 270 160 292 240 286 C320 280 400 300 480 296 C560 292 640 304 720 296 C800 290 860 300 920 296 L920 470 L0 470 Z" opacity="0.35"/>
    <path fill="var(--paper)" d="M0 540 C40 532 70 540 100 534 C140 520 180 510 220 518 C250 524 260 540 280 550 C300 566 330 580 360 584 C400 588 440 590 480 588 C520 584 560 574 600 560 C640 548 680 530 720 520 C760 512 800 500 840 506 C870 510 900 502 920 504 L920 710 L0 710 Z"/>
  </svg>
  <div class="house-photo" role="img" aria-label="Faded blue-tinted photograph of an old stone house in Greece with a tiled roof and wooden shutters"></div>
  <div class="author-portrait" role="img" aria-label="Portrait photograph of the author in a navy blazer with arms crossed"></div>

  <h2 class="back-title">Leaving Harbor</h2>
  <p class="blurb blurb-lead">Lorem ipsum dolor sit amet, consectetur adipiscing elit, sed do eiusmod tempor incididunt ut labore et dolore magna aliqua. Quis ipsum suspendisse ultrices gravida. Risus commodo viverra maecenas accumsan lacus vel facilisis. Lorem ipsum dolor sit amet, consectetur adipiscing elit, sed do eiusmod tempor incididunt ut labore et dolore magna</p>
  <p class="blurb blurb-more">Quis ipsum suspendisse ultrices gravida. Risus commodo viverra maecenas accumsan lacus vel facilisis. Lorem ipsum dolor sit amet, consectetur adipiscing elit, sed do eiusmod tempor incididunt ut labore et dolore magna aliqua. Quis ipsum suspendisse ultrices gravida. Risus commodo viverra maecenas accumsan lacus vel facilisis.</p>
  <p class="isbn">ISBN: 978-1-5523094-1-0</p>

  <h1 class="front-title">Leaving Harbor</h1>
  <p class="author-name">Kevin Marlow</p>
</main>
</body>
</html>
```